Stationery Design Project

I need a stationary design for our company. we are based in Houston, TX and we are called Mira Vell Lending. And we are wanting to brand our MoneyMendPlus program, which includes our tax preparation and restoration, credit repair service. Although our business offers other programs, we are interested in mainly focusing on The MoneyMendPlus program. We are looking for way to brand our ourselves and I believe that a great stationery design will help in achieving this goal. Our logo design is blue and light blue. the slogan is orange.

Industry/Entity Type

Business

Requirements
Must have
• Address: 30871 Calloway Ln. B-22
Houston, TX 75419
Tel. 555-318-6207
Fax 555-294-7153
www.miravelllending.example
info@miravelllending.example
Our Slogan: Balance, Renewed.

```html
<!DOCTYPE html>
<html lang="en">
<head>
<meta charset="utf-8">
<title>MoneyMendPlus Business Card</title>
<link href="https://fonts.googleapis.com/css2?family=Tinos:wght@400;700&display=swap" rel="stylesheet">
<style>
  :root {
    --backdrop: #ececec;
    --card: #ffffff;
    --navy: #14406a;
    --blue: #1a6aa8;
    --sky: #1b8fcf;
    --ink: #2a2a2a;
    --muted: #555555;
    --rule: #c8c8c8;
  }
  * { margin: 0; padding: 0; box-sizing: border-box; }
  html, body { width: 1200px; height: 1071px; overflow: hidden; }
  body {
    background: var(--backdrop);
    font-family: "Tinos", "Times New Roman", serif;
    color: var(--ink);
    position: relative;
  }
  .card {
    position: absolute;
    width: 780px;
    height: 450px;
    background: var(--card);
    box-shadow: 0 2px 10px rgba(0,0,0,0.18);
    overflow: hidden;
  }
  .card-front { left: 60px; top: 60px; }
  .card-back { left: 360px; top: 570px; }

  .program-name {
    position: absolute;
    left: 0; right: 0; top: 120px;
    text-align: center;
    font-size: 68px;
    line-height: 1.2;
    color: var(--blue);
    font-weight: 400;
  }
  .slogan {
    position: absolute;
    left: 0; right: 0; top: 215px;
    text-align: center;
    font-size: 24px;
    font-weight: 400;
    color: var(--muted);
  }
  .address {
    position: absolute;
    right: 440px; top: 300px;
    text-align: right;
    font-size: 21px;
    line-height: 1.4;
  }
  .divider {
    position: absolute;
    left: 360px; top: 285px;
    width: 1px; height: 125px;
    background: var(--rule);
  }
  .contacts {
    position: absolute;
    left: 385px; top: 285px;
    list-style: none;
    font-size: 20px;
    line-height: 31px;
  }
  .contacts li { display: flex; align-items: center; gap: 10px; }
  .contacts svg { width: 17px; height: 17px; fill: var(--navy); flex: none; }
  .band {
    position: absolute;
    left: 0; right: 0; bottom: 0;
    height: 26px;
    background: linear-gradient(90deg, var(--sky), var(--navy));
  }

  .company {
    position: absolute;
    left: 0; right: 0; top: 170px;
    display: flex; align-items: center; justify-content: center; gap: 16px;
  }
  .company-square { width: 38px; height: 38px; background: var(--navy); }
  .company-name { font-size: 44px; color: var(--navy); }
  .web-address {
    position: absolute;
    left: 0; right: 0; top: 340px;
    text-align: center;
    font-size: 22px;
    letter-spacing: 6px;
    color: var(--ink);
  }
  .web-address strong { color: var(--navy); font-size: 26px; }
</style>
</head>
<body>
  <section class="card card-front" aria-label="Card front">
    <h1 class="program-name">MoneyMendPlus</h1>
    <p class="slogan">Balance, Renewed.</p>
    <p class="address">30871 Calloway Ln. B-22<br>Houston, TX 75419</p>
    <div class="divider"></div>
    <ul class="contacts">
      <li>
        <svg viewBox="0 0 16 16" aria-hidden="true"><path d="M3.6 1.5l2.3 2.4-1.3 1.9c.9 2 2.6 3.7 4.6 4.6l1.9-1.3 2.4 2.3-1.4 2.3C6.8 13.6 2.4 9.2 1.3 2.9z"/></svg>
        555-318-6207
      </li>
      <li>
        <svg viewBox="0 0 16 16" aria-hidden="true"><path d="M4 1h8v4H4z M1 6h14v7h-2v2H3v-2H1z M4 10v4h8v-4z" fill-rule="evenodd"/></svg>
        555-294-7153
      </li>
      <li>
        <svg viewBox="0 0 16 16" aria-hidden="true"><path d="M1 4h14v9H1z M2 5l6 4.5L14 5v-.2H2z" fill-rule="evenodd"/></svg>
        info@miravelllending.example
      </li>
      <li>
        <svg viewBox="0 0 16 16" aria-hidden="true"><circle cx="8" cy="8" r="6.5" fill="none" stroke="#14406a" stroke-width="1.4"/><path d="M1.5 8h13M8 1.5v13" stroke="#14406a" stroke-width="1.1"/><ellipse cx="8" cy="8" rx="3" ry="6.5" fill="none" stroke="#14406a" stroke-width="1.1"/></svg>
        www.miravelllending.example
      </li>
    </ul>
    <div class="band"></div>
  </section>

  <section class="card card-back" aria-label="Card back">
    <div class="company">
      <span class="company-square"></span>
      <span class="company-name">Mira Vell Lending</span>
    </div>
    <p class="web-address">www.<strong>miravelllending</strong>.example</p>
  </section>
</body>
</html>
```